Redesign Website - Current one too plain

The description is in the uploaded file. Please let me know if you need any more information. I'd prefer it if someone could implement the design to a WordPress site but the best design will win, regardless.
I would like the forms to look nice as well
UPDATE:
I don't think we can use the images that I provided, I think they make the site look a bit 'cheap' and I really don't know how to replace them. One thought I have had is to make the "Simple, Unique, Effective" a second feature on the right side of the page with the search on the left
Target Market(s)
Small companies, private sellers of cars and people who rent their caravan/holiday home out
Industry/Entity Type
Advertising
Number of Pages Required
3 page
Colors
Designer to choose colors to be used in the design.
Look and feel
Each slider illustrates characteristics of the customer's brand and the style your logo design should communicate.

```html
<!DOCTYPE html>
<html lang="en">
<head>
<meta charset="utf-8">
<title>Kodera – Find advertisers by their code</title>
<link href="https://fonts.googleapis.com/css2?family=Baloo+2:wght@600;700;800&family=Barlow:wght@400;500;600;700&display=swap" rel="stylesheet">
<style>
:root{
  --lime:#e5ff00;
  --dark:#2a2a2a;
  --darker:#222222;
  --tile:#323232;
  --chip:#3d3d3d;
  --light:#f3f3f3;
  --white:#ffffff;
  --ink:#2a2a2a;
  --muted:#6d6d6d;
}
*{box-sizing:border-box;margin:0;padding:0}
html,body{width:1200px;height:3182px;overflow:hidden}
body{position:relative;font-family:"Barlow",sans-serif;color:var(--ink);background:var(--white)}
.abs{position:absolute}
.center{text-align:center}

/* header + hero */
.hero{position:absolute;left:0;top:0;width:1200px;height:685px;
  background:radial-gradient(ellipse 420px 300px at 600px 520px,#6e6e6e 0%,#3e3e3e 55%,var(--dark) 100%)}
.brand{position:absolute;display:flex;align-items:center;gap:14px;font-family:"Barlow",sans-serif;font-weight:700;color:var(--lime);letter-spacing:8px}
.brand-dot{background:var(--lime);border-radius:50%}
.brand--header{left:118px;top:36px;font-size:36px}
.brand--header .brand-dot{width:30px;height:30px}
.nav{position:absolute;top:50px;left:0;width:1200px;font-size:15px;font-weight:500;color:var(--white)}
.nav a{position:absolute;color:inherit;text-decoration:none}
.nav a.active{color:var(--lime)}

.search-panel{position:absolute;left:293px;top:120px;width:614px;height:258px;background:var(--darker);border-radius:3px}
.code-tile{position:absolute;top:59px;width:124px;height:130px;background:var(--tile);border-radius:2px;
  font-family:"Baloo 2",sans-serif;font-weight:800;font-size:150px;line-height:160px;color:var(--lime);text-align:center}
.tile-arrow{position:absolute;width:0;height:0;border-left:5px solid transparent;border-right:5px solid transparent}
.tile-arrow.up{border-bottom:6px solid var(--lime)}
.tile-arrow.down{border-top:6px solid var(--lime)}
.chip{position:absolute;top:93px;height:31px;border-radius:16px;background:var(--chip);color:var(--lime);
  font-size:14px;font-weight:500;line-height:31px;text-align:center}
.search-btn{position:absolute;left:302px;top:137px;width:106px;height:30px;border-radius:15px;background:var(--lime);
  color:var(--ink);font-size:14px;font-weight:600;line-height:30px;text-align:center}
.vehicles{position:absolute;left:226px;top:389px;width:768px;height:302px;
  background:radial-gradient(ellipse 380px 150px at 50% 60%,#b9b9b9 0%,#8d8d8d 45%,rgba(90,90,90,0) 80%)}

/* features */
.features{position:absolute;left:0;top:685px;width:1200px;height:542px;background:var(--light)}
.feature{position:absolute;top:100px;width:336px;height:336px;border-radius:50%;background:var(--white);
  box-shadow:0 10px 28px rgba(0,0,0,.12);text-align:center}
.feature--ring{box-shadow:0 0 0 8px #ececec,0 10px 28px rgba(0,0,0,.1)}
.feature-icon{position:absolute;left:121px;top:64px;width:94px;height:94px;border-radius:50%;background:var(--lime)}
.feature-title{position:absolute;left:0;top:166px;width:336px;font-family:"Baloo 2",sans-serif;font-weight:700;font-size:15px;color:var(--ink)}
.feature-text{position:absolute;left:48px;top:195px;width:240px;font-size:14px;line-height:21px;color:var(--muted)}

/* testimonials */
.section-title{position:absolute;left:0;width:1200px;text-align:center;font-family:"Baloo 2",sans-serif;font-weight:800;font-size:48px;line-height:1}
.testimonial{position:absolute;top:1416px;width:339px;height:383px;background:var(--dark);border-radius:4px;color:var(--white);text-align:center}
.avatar{position:absolute;left:110px;top:29px;width:119px;height:119px;border-radius:50%;border:3px solid var(--lime);
  background:linear-gradient(160deg,#d8d3cc,#8b7b6c)}
.quote-text{position:absolute;left:40px;top:153px;width:259px;font-size:14px;line-height:21.5px}
.quote-name{position:absolute;left:0;top:318px;width:339px;font-size:18px;font-weight:700}
.quote-mark{position:absolute;left:262px;top:340px;font-family:"Baloo 2",sans-serif;font-weight:800;font-size:90px;line-height:1;color:var(--lime)}
.slider-arrow{position:absolute;top:1596px}

/* advertise */
.advertise{position:absolute;left:0;top:1917px;width:1200px;height:374px;
  background:radial-gradient(ellipse 520px 330px at 600px 110px,#8a8a8a 0%,#5a5a5a 45%,var(--dark) 100%);color:var(--white)}
.advertise-text{position:absolute;left:262px;top:130px;width:676px;font-size:14px;line-height:26px;text-align:center}
.pill-btn{position:absolute;height:41px;border-radius:21px;background:var(--lime);color:var(--ink);font-size:14px;font-weight:600;line-height:41px;text-align:center}

/* contact */
.field{position:absolute;height:44px;border-radius:22px;background:var(--white);box-shadow:0 4px 14px rgba(0,0,0,.1);
  font-size:14px;color:#666;padding:13px 0 0 22px}
.field--message{height:166px;border-radius:30px;padding-top:20px}

/* footer */
.footer{position:absolute;left:0;top:2858px;width:1200px;height:324px;
  background:radial-gradient(ellipse 480px 260px at 600px 170px,#6c6c6c 0%,#434343 50%,var(--dark) 100%);color:var(--white)}
.brand--footer{left:466px;top:90px;font-size:62px;letter-spacing:14px;gap:22px}
.brand--footer .brand-dot{width:50px;height:50px}
.footer-nav{position:absolute;top:204px;left:0;width:1200px;display:flex;justify-content:center;gap:30px;font-size:14px;font-weight:500}
.copyright{position:absolute;top:246px;left:0;width:1200px;text-align:center;font-size:14px}
</style>
</head>
<body>

<header class="hero">
  <div class="brand brand--header"><span class="brand-dot"></span>KODERA</div>
  <nav class="nav">
    <a class="active" style="left:735px">Home</a>
    <a style="left:802px">Advertise</a>
    <a style="left:891px">Contact</a>
    <a style="left:970px">Register</a>
    <a style="left:1053px">Login</a>
  </nav>

  <section class="search-panel" aria-label="Code search">
    <span class="tile-arrow up" style="left:78px;top:34px"></span>
    <span class="tile-arrow up" style="left:215px;top:34px"></span>
    <div class="code-tile" style="left:23px">A</div>
    <div class="code-tile" style="left:158px">1</div>
    <span class="tile-arrow down" style="left:78px;top:212px"></span>
    <span class="tile-arrow down" style="left:215px;top:212px"></span>
    <div class="chip" style="left:302px;width:63px">CAR</div>
    <div class="chip" style="left:371px;width:96px">CARAVAN</div>
    <div class="chip" style="left:474px;width:105px">COMPANY</div>
    <div class="search-btn">SEARCH</div>
  </section>

  <div class="vehicles" role="img" aria-label="Photo of a car, a static caravan and a van, each showing a short advertising code"></div>
</header>

<section class="features">
  <div class="feature" style="left:111px">
    <div class="feature-icon">
      <svg width="94" height="94" viewBox="0 0 94 94" fill="none" stroke="#222" stroke-width="2.2">
        <circle cx="33" cy="35" r="8"/><circle cx="33" cy="35" r="3"/>
        <circle cx="61" cy="35" r="8"/><circle cx="61" cy="35" r="3"/>
        <circle cx="47" cy="58" r="10"/><path d="M42 58l4 4 7-7"/>
      </svg>
    </div>
    <div class="feature-title">Simple</div>
    <div class="feature-text">create&nbsp; your advert and display your code</div>
  </div>
  <div class="feature feature--ring" style="left:431px">
    <div class="feature-icon">
      <svg width="94" height="94" viewBox="0 0 94 94" fill="none" stroke="#222" stroke-width="2.2">
        <circle cx="43" cy="43" r="16"/><circle cx="43" cy="43" r="10"/><circle cx="43" cy="43" r="4"/>
        <path d="M55 55l12 12" stroke-width="4" stroke-linecap="round"/>
      </svg>
    </div>
    <div class="feature-title">Unique</div>
    <div class="feature-text">customers find you by an easy-to-remember code</div>
  </div>
  <div class="feature" style="left:750px">
    <div class="feature-icon">
      <svg width="94" height="94" viewBox="0 0 94 94" fill="none" stroke="#222" stroke-width="2.2">
        <path d="M30 64V52M42 64V44M54 64V38M66 64V30"/>
        <path d="M28 46l14-10 10 6 16-14M60 28h8v8"/>
        <path d="M24 66h46"/>
      </svg>
    </div>
    <div class="feature-title">Effective</div>
    <div class="feature-text">customers are directed to you and not a list of your competitors</div>
  </div>
</section>

<h2 class="section-title" style="top:1312px">Customer Testimonials</h2>

<svg class="slider-arrow" style="left:108px" width="20" height="24" viewBox="0 0 20 24" fill="none" stroke="#2a2a2a" stroke-width="2.5"><path d="M14 2L4 12l10 10"/></svg>
<svg class="slider-arrow" style="left:1071px" width="20" height="24" viewBox="0 0 20 24" fill="none" stroke="#2a2a2a" stroke-width="2.5"><path d="M6 2l10 10L6 22"/></svg>

<article class="testimonial" style="left:186px">
  <div class="avatar" role="img" aria-label="Portrait photo of the customer"></div>
  <p class="quote-text">“Lorem ipsum dolor sit amet, consectetur adipiscing elit, sed do eiusmod tempor incididunt ut labore et dolore magna aliqua. Ut enim ad minim veniam, quis nostrud exercitation ullamco laboris nisi ut aliquip ex ea commodo consequat.”</p>
  <div class="quote-name">John Doe</div>
  <div class="quote-mark">“</div>
</article>
<article class="testimonial" style="left:675px">
  <div class="avatar" role="img" aria-label="Portrait photo of the customer"></div>
  <p class="quote-text">“Lorem ipsum dolor sit amet, consectetur adipiscing elit, sed do eiusmod tempor incididunt ut labore et dolore magna aliqua. Ut enim ad minim veniam, quis nostrud exercitation ullamco laboris nisi ut aliquip ex ea commodo consequat.”</p>
  <div class="quote-name">Daniel</div>
  <div class="quote-mark">“</div>
</article>

<section class="advertise">
  <h2 class="section-title" style="top:71px;color:var(--white)">Advertise</h2>
  <p class="advertise-text">Lorem ipsum dolor sit amet, consectetur adipiscing elit, sed do eiusmod tempor incididunt ut labore et dolore magna aliqua. Ut enim ad minim veniam, quis nostrud exercitation ullamco laboris nisi ut aliquip ex ea commodo consequat.</p>
  <div class="pill-btn" style="left:528px;top:231px;width:144px">VIEW DETAILS</div>
</section>

<h2 class="section-title" style="top:2380px">Contact Us</h2>
<div class="field" style="left:222px;top:2451px;width:235px">Name</div>
<div class="field" style="left:483px;top:2451px;width:236px">Email</div>
<div class="field" style="left:744px;top:2451px;width:236px">Phone</div>
<div class="field field--message" style="left:218px;top:2525px;width:764px">Message</div>
<div class="pill-btn" style="left:528px;top:2712px;width:144px">SUBMIT NOW</div>

<footer class="footer">
  <div class="brand brand--footer"><span class="brand-dot"></span>KODERA</div>
  <nav class="footer-nav"><span>Home</span><span>Advertise</span><span>Contact</span><span>Register</span><span>Login</span></nav>
  <div class="copyright">© Copyrights 2023 | All Rights Reserved</div>
</footer>

</body>
</html>
```